CREATE A BUSINESS CARD FOR A BOAT CLEANING SERVICE

WE ARE STARTING A NEW BOAT CLEANING BUSINESS. WE DIVE UNDERWATER TO CLEAN BOAT HULLS, JETTIES, UNDERWATER STRUCTURES ETC. WE ARE LOOKING FOR AN UPPERMARKET MODERN LOGO AND BUSINESS CARD AS ALOT OF OUR TARGET MARKET WILL BE HIGH END. YOU HAVE TO DESIGN A BUSINESS CARD AND LOGO SEPERATELY .
THE BUSINESS CARD DIMESNION MUST BE STANDARD SIZE.
The standard dimensions of a printed business card are 3.5 x 2 inches

Target Market(s)

UNDERWATER SERVICED

Industry/Entity Type

Business

Contact Information for Business Card

HOLLAND UNDERWATER SERVICES

Font styles to use
Serif

Colors

Designer to choose colors to be used in the design.

Requirements
Must have
• HOLLAND
Nice to have
• dark
Should not have
• more than 3 colors

```html
<!DOCTYPE html>
<html lang="en">
<head>
<meta charset="utf-8">
<title>Holland Underwater Service – Business Card</title>
<link href="https://fonts.googleapis.com/css2?family=Lato:wght@400&display=swap" rel="stylesheet">
<style>
  :root {
    --navy: #174f88;
    --white: #ffffff;
    --stage: #ecebe8;
    --sub-grey: #5d6470;
  }
  * { margin: 0; padding: 0; box-sizing: border-box; }
  html, body { width: 1200px; height: 900px; overflow: hidden; }
  body {
    background: var(--stage);
    font-family: "Lato", Arial, sans-serif;
    position: relative;
  }
  .card {
    position: absolute;
    top: 150px;
    width: 343px;
    height: 600px;
    overflow: hidden;
  }
  .card--front { left: 246px; background: var(--white); }
  .card--back { left: 611px; background: var(--navy); color: var(--white); }

  .wordmark { position: absolute; left: 0; width: 100%; text-align: center; font-weight: 400; }
  .front-wordmark { top: 126px; color: var(--navy); }
  .wordmark__name { display: block; font-size: 24px; letter-spacing: 11px; padding-left: 11px; }
  .wordmark__sub { display: block; font-size: 12.5px; letter-spacing: 3.6px; padding-left: 3.6px; margin-top: 6px; }

  .front-band { position: absolute; left: 0; top: 0; width: 343px; height: 600px; }

  .holder { position: absolute; left: 33px; top: 318px; color: var(--white); }
  .holder__name { font-size: 19.5px; letter-spacing: 0.6px; line-height: 1.1; }
  .holder__role { font-size: 17px; line-height: 1.2; margin-top: 1px; }

  .contacts { position: absolute; left: 33px; top: 381px; list-style: none; color: var(--white); font-size: 14.2px; }
  .contacts li { display: flex; align-items: center; height: 19.5px; }
  .contacts svg { width: 11px; height: 11px; margin-right: 13px; flex: none; }

  .address { position: absolute; left: 33px; top: 456px; color: var(--white); font-size: 14.2px; line-height: 19.5px; font-style: normal; }

  .footer-marks { position: absolute; left: 33px; top: 524px; display: flex; align-items: center; }
  .footer-marks__name { color: var(--white); font-size: 24px; letter-spacing: 0.5px; }
  .partner-badge { margin-left: 38px; width: 68px; height: 44px; }

  .back-wordmark { top: 312px; color: var(--white); }
  .back-wordmark .wordmark__name { font-size: 33px; letter-spacing: 17px; padding-left: 17px; }
  .back-wordmark .wordmark__sub { font-size: 17px; letter-spacing: 5px; padding-left: 5px; margin-top: 8px; }
  .back-url { position: absolute; left: 0; width: 100%; top: 528px; text-align: center; font-size: 14.5px; letter-spacing: 0.3px; }
</style>
</head>
<body>
  <section class="card card--front" aria-label="Business card front">
    <div class="wordmark front-wordmark">
      <span class="wordmark__name">HOLLAND</span>
      <span class="wordmark__sub" style="color: var(--navy);">UNDERWATER SERVICE</span>
    </div>

    <svg class="front-band" viewBox="0 0 343 600" aria-hidden="true">
      <polygon points="0,330 343,262 343,600 0,600" fill="var(--navy)"/>
      <polygon points="0,300 343,206 343,228 0,318" fill="var(--navy)"/>
      <line x1="0" y1="324" x2="343" y2="245" stroke="var(--white)" stroke-width="0" />
    </svg>

    <div class="holder">
      <div class="holder__name">DAAN VERHOEF</div>
      <div class="holder__role">CEO / Founder</div>
    </div>

    <ul class="contacts">
      <li>
        <svg viewBox="0 0 12 12" aria-hidden="true"><path d="M2.4 0.6 L4.2 2.8 L3.2 4.2 C3.9 5.7 5.1 7 6.8 7.9 L8 6.8 L11.2 8.4 L10.4 10.6 C5.5 10.6 1.2 6.4 0.6 1.6 Z" fill="var(--white)"/></svg>
        212-555-0147
      </li>
      <li>
        <svg viewBox="0 0 12 12" aria-hidden="true"><rect x="0.5" y="2" width="11" height="8" fill="var(--white)"/><path d="M0.5 2 L6 6.6 L11.5 2" fill="none" stroke="var(--navy)" stroke-width="1"/></svg>
        info@hollandunderwaterservice.com
      </li>
      <li>
        <svg viewBox="0 0 12 12" aria-hidden="true" fill="none" stroke="var(--white)" stroke-width="1"><circle cx="6" cy="6" r="5.2"/><ellipse cx="6" cy="6" rx="2.2" ry="5.2"/><line x1="0.8" y1="6" x2="11.2" y2="6"/><line x1="1.6" y1="3.4" x2="10.4" y2="3.4"/><line x1="1.6" y1="8.6" x2="10.4" y2="8.6"/></svg>
        www.hollandunderwaterservice.com
      </li>
    </ul>

    <address class="address">
      Kademolen 22 4817XK<br>
      Breda, The Netherlands
    </address>

    <div class="footer-marks">
      <span class="footer-marks__name">HOLLAND</span>
      <svg class="partner-badge" viewBox="0 0 68 44" role="img" aria-label="Partner badge">
        <ellipse cx="34" cy="22" rx="33" ry="21" fill="#2f6ea5"/>
      </svg>
    </div>
  </section>

  <section class="card card--back" aria-label="Business card back">
    <div class="wordmark back-wordmark">
      <span class="wordmark__name">HOLLAND</span>
      <span class="wordmark__sub">UNDERWATER SERVICE</span>
    </div>
    <div class="back-url">www.hollandunderwaterservice.com</div>
  </section>
</body>
</html>
```